New Business Card Design Project

I need a design for business cards, i am an electrical business called "Corvane Electrical and Communications" i need the cards to be double sided with the company logo on the back (attached) the front needs to say my company name, web site, email address, telephone number, and ABN number and electrical license number. I am open to different arrangements of the information but would like the background to be incorporating something electrical or something that looks smart. open to all additional ideas also.

The company colours are orange and grey see logo attached.

Business Name: Corvane Electrical and Communications
Website: corvaneelectricalandcomms.example.com.au
Email: brent@corvaneelectricalandcomms.example.com.au
Telephone(mobile): 0481209736
ABN: 71208349162
Lic No: 418273D

Target Market(s)

Business entities, Project Managers, Accounts, Clients

Industry/Entity Type

Electrician

Contact Information for Business Card

I need a design for business cards, i am an electrical business called "Corvane Electrical and Communications" i need the cards to be double sided with the company logo on the back (attached) the front needs to say my company name

Font styles to use
Serif
Sans Serif

Colors
f37122
5c5c5c

Requirements
Must have
• Must have the Logo on the back open to different ways of it being on the back but had in mind to keep it central but again open to other options
Nice to have
• A real modern cool background that is eye catching yet contemporary
Should not have
• No backgrounds of a light bulb or plug or anything like that

```html
<!DOCTYPE html>
<html lang="en">
<head>
<meta charset="utf-8">
<title>Corvane Electrical and Communications – Business Cards</title>
<link rel="stylesheet" href="https://fonts.googleapis.com/css2?family=Ubuntu:wght@400;500&display=swap">
<style>
  :root {
    --canvas: #e9e6e1;
    --paper: #f4f4f3;
    --grey: #5e5e60;
    --grey-dark: #4c4c4e;
    --grey-light: #6c6c6e;
    --accent: #e6b21c;
    --accent-deep: #d9a514;
    --white: #ffffff;
  }
  * { box-sizing: border-box; margin: 0; padding: 0; }
  html, body { width: 1200px; height: 780px; overflow: hidden; }
  body {
    background: var(--canvas);
    font-family: "Ubuntu", sans-serif;
    position: relative;
  }
  .card {
    position: absolute;
    top: 240px;
    width: 520px;
    height: 300px;
    border-radius: 4px;
    overflow: hidden;
    box-shadow: 0 6px 18px rgba(0,0,0,0.18);
  }
  .card--front { left: 50px; background: var(--paper); }
  .card--back {
    left: 630px;
    background: linear-gradient(135deg, var(--grey-light), var(--grey) 55%, var(--grey-dark));
  }

  /* front */
  .front-brand {
    position: absolute; left: 0; top: 0; width: 100%; height: 138px;
    padding: 30px 0 0 34px;
  }
  .brand-name {
    font-weight: 400;
    color: var(--grey);
    letter-spacing: 4px;
    line-height: 1;
  }
  .front-brand .brand-name--main { font-size: 56px; }
  .front-brand .brand-name--sub { font-size: 14px; letter-spacing: 2.2px; margin-top: 8px; }

  .front-contact {
    position: absolute; left: 0; top: 138px; width: 100%; height: 118px;
    background: var(--grey);
    display: flex; align-items: center;
    padding: 0 20px 0 28px;
  }
  .person { width: 150px; color: var(--white); }
  .person__name { font-size: 21px; font-weight: 400; }
  .person__role { font-size: 15px; color: var(--accent); margin-top: 3px; }
  .divider { width: 1px; height: 58px; background: #9a9a9c; margin: 0 16px 0 8px; }
  .contact-list { list-style: none; color: var(--white); font-size: 11px; }
  .contact-list li { display: flex; align-items: center; margin: 5px 0; }
  .contact-list .icon {
    width: 14px; height: 14px; background: var(--accent);
    border-radius: 2px; margin-right: 7px; flex: none;
  }
  .contact-list .phone-number { font-size: 13px; }

  .front-strip {
    position: absolute; left: 0; bottom: 0; width: 100%; height: 44px;
    background: var(--accent);
    display: flex; justify-content: space-between; align-items: center;
    padding: 0 28px;
    color: var(--grey-dark); font-size: 13px;
  }

  /* back */
  .back-brand {
    position: absolute; left: 0; top: 0; width: 100%; height: 256px;
    display: flex; flex-direction: column; align-items: center; justify-content: center;
  }
  .back-brand .brand-name { color: var(--white); }
  .back-brand .brand-name--main { font-size: 60px; letter-spacing: 5px; }
  .back-brand .brand-name--sub { font-size: 14px; letter-spacing: 2.4px; margin-top: 10px; }
  .back-strip {
    position: absolute; left: 0; bottom: 0; width: 100%; height: 44px;
    background: linear-gradient(90deg, var(--accent-deep), var(--accent));
    display: flex; align-items: center; padding: 0 28px;
    color: var(--grey-dark); font-size: 13px;
  }
</style>
</head>
<body>

<section class="card card--front" aria-label="Business card front">
  <header class="front-brand">
    <p class="brand-name brand-name--main">CORVANE</p>
    <p class="brand-name brand-name--sub">ELECTRICAL &amp; COMMUNICATIONS</p>
  </header>

  <div class="front-contact">
    <div class="person">
      <p class="person__name">Employee Name</p>
      <p class="person__role">Principal</p>
    </div>
    <span class="divider"></span>
    <ul class="contact-list">
      <li>
        <svg class="icon" viewBox="0 0 14 14" aria-hidden="true"><rect x="4.5" y="2.5" width="5" height="9" rx="1" fill="none" stroke="#5e5e60" stroke-width="1.2"/></svg>
        <span class="phone-number">0481209736</span>
      </li>
      <li>
        <svg class="icon" viewBox="0 0 14 14" aria-hidden="true"><rect x="2.5" y="4" width="9" height="6.5" fill="none" stroke="#5e5e60" stroke-width="1.2"/><path d="M2.5 4 L7 8 L11.5 4" fill="none" stroke="#5e5e60" stroke-width="1.2"/></svg>
        <span>brent@corvaneelectricalandcomms.example.com.au</span>
      </li>
      <li>
        <svg class="icon" viewBox="0 0 14 14" aria-hidden="true"><circle cx="7" cy="7" r="4.3" fill="none" stroke="#5e5e60" stroke-width="1.1"/><ellipse cx="7" cy="7" rx="1.8" ry="4.3" fill="none" stroke="#5e5e60" stroke-width="1"/><path d="M2.7 7 H11.3" stroke="#5e5e60" stroke-width="1"/></svg>
        <span>corvaneelectricalandcomms.example.com.au</span>
      </li>
    </ul>
  </div>

  <footer class="front-strip">
    <span class="licence">Lic No: 418273D</span>
    <span class="abn">ABN: 71208349162</span>
  </footer>
</section>

<section class="card card--back" aria-label="Business card back">
  <div class="back-brand">
    <p class="brand-name brand-name--main">CORVANE</p>
    <p class="brand-name brand-name--sub">ELECTRICAL &amp; COMMUNICATIONS</p>
  </div>
  <footer class="back-strip">
    <span>corvaneelectricalandcomms.example.com.au</span>
  </footer>
</section>

</body>
</html>
```